Kelvor Engineers: Why you should hire us keepsake

New design. Open to plastic cards. We are an engineering firm that designs cell phone towers and commercial buildings. Please check out our website www.kelvorstruct.com for more details. We want people to remember our card and for it to be useful if possible. We want the same look and feel on these cards to be translated to other marketing material we may need such as brochures.

Target Market(s)

Architects, Developers and Telecommunication Carriers

Industry/Entity Type

Engineering

Contact Information for Business Card

Card with our company colors, logo, and innovative design with elements related to our industry.

Font styles to use
Sans Serif

Colors
9bcb3c
abd036
0255a3

Requirements
Must have
• Sleek and hip design
Nice to have
• Bright lime green and navy coloring that pops with an innovative design.
Should not have
• A basic and boring design

```html
<!DOCTYPE html>
<html lang="en">
<head>
<meta charset="utf-8">
<title>Kelvor Engineers – Business Card</title>
<link rel="stylesheet" href="https://fonts.googleapis.com/css2?family=Roboto:wght@400;700&family=Roboto+Condensed:wght@700&display=swap">
<style>
  :root {
    --lime: #16f51a;
    --navy: #0b2c58;
    --paper: #f3f3f3;
    --ink: #555555;
    --backdrop: #2b2b2b;
  }
  * { margin: 0; padding: 0; box-sizing: border-box; }
  html, body { width: 1200px; height: 960px; overflow: hidden; }
  body {
    background: var(--backdrop);
    position: relative;
    font-family: "Roboto", Arial, sans-serif;
  }
  .card {
    position: absolute;
    left: 320px;
    width: 600px;
    height: 344px;
    background: var(--paper);
    border-radius: 18px;
    overflow: hidden;
  }
  .card-front { top: 104px; }
  .card-back { top: 492px; }

  .brand-name {
    position: absolute;
    left: 0; right: 0;
    top: 128px;
    text-align: center;
    font-weight: 700;
    font-size: 52px;
    letter-spacing: -1px;
    color: var(--lime);
  }
  .tagline {
    position: absolute;
    left: 0; right: 0;
    top: 269px;
    display: flex;
    justify-content: center;
    align-items: center;
    gap: 3px;
    font-weight: 700;
    font-size: 16px;
    letter-spacing: 0.3px;
    color: var(--lime);
  }
  .tagline::before, .tagline::after {
    content: "";
    width: 28px;
    height: 2px;
    background: var(--navy);
  }
  .locations {
    position: absolute;
    left: 0; right: 0;
    top: 291px;
    text-align: center;
    font-size: 15px;
    letter-spacing: 1px;
    color: var(--ink);
  }

  .hex-field {
    position: absolute;
    left: 0; top: 0;
    width: 600px; height: 344px;
  }
  .holder-name {
    position: absolute;
    left: 360px;
    top: 189px;
    font-family: "Roboto Condensed", "Arial Narrow", sans-serif;
    font-weight: 700;
    font-size: 21px;
    color: var(--lime);
  }
  .contact-list {
    position: absolute;
    left: 362px;
    top: 224px;
    list-style: none;
    font-size: 14px;
    color: var(--ink);
  }
  .contact-list li {
    display: flex;
    align-items: center;
    gap: 10px;
    height: 19px;
  }
  .contact-list svg { width: 12px; height: 12px; fill: var(--lime); flex: none; }
</style>
</head>
<body>

<section class="card card-front">
  <div class="brand-name">Kelvor Engineers</div>
  <div class="tagline">MULTI-DISCIPLINE ENGINEERING</div>
  <div class="locations">Augusta | Richmond | El Paso | Sacramento</div>
</section>

<section class="card card-back">
  <svg class="hex-field" viewBox="0 0 600 344" role="img" aria-label="Diagonal field of lime green and navy hexagons">
    <defs>
      <linearGradient id="hexTone" x1="0" y1="1" x2="1" y2="0">
        <stop offset="0" stop-color="var(--lime)"/>
        <stop offset="0.55" stop-color="var(--navy)"/>
        <stop offset="1" stop-color="var(--navy)"/>
      </linearGradient>
    </defs>
    <polygon points="0,0 565,0 330,170 170,344 0,344" fill="url(#hexTone)"/>
  </svg>

  <div class="holder-name">DANA HOLLOWAY REYES</div>
  <ul class="contact-list">
    <li><svg viewBox="0 0 12 12"><path d="M2.5 0.5l2 2.3-1 1.4c.7 1.5 1.8 2.6 3.3 3.3l1.4-1 2.3 2-1 2.4C5 10.5 1.5 7 0.1 1.5z"/></svg>555.201.4410</li>
    <li><svg viewBox="0 0 12 12"><path d="M3 0h6v12H3zM4.2 1.5v8h3.6v-8z"/></svg>555.318.7623</li>
    <li><svg viewBox="0 0 12 12"><path d="M0 2h12v1.2L6 7 0 3.2zM0 4.6l6 3.8 6-3.8V10H0z"/></svg>dreyes@kelvorstruct.com</li>
    <li><svg viewBox="0 0 12 12"><circle cx="6" cy="6" r="6"/></svg>www.kelvorstruct.com</li>
  </ul>
</section>

</body>
</html>
```